Global Yoga Apparel Brand Needs a Beautiful Website

We need a website design for a new Yoga brand called Vey. We develop beautiful, stylish, sexy, comfortable yoga leggings, tops, and yoga apparel for women looking to feel their best, look their best and perform their best on and off the yoga mat.
This will go up at http://vey.example/ (which is a landing page right now).
We would like to see simple and clean design where the focus will be on powerful images and clean background space. We will be using Shopify to start building on and here are three sites that we would love to see options based off of the look, layout and feel while making something unique at the same time:
1. Dunt.ca
2. parvasini.com
3. www.k-mole.com
The final design should look clean, beautiful, inspiring, powerful and empowering.
Target Market(s)
mostly Females 21-35 range but will be appealing to women over 35 as well.

```html
<!DOCTYPE html>
<html lang="en">
<head>
<meta charset="utf-8">
<title>Vey Yoga</title>
<link href="https://fonts.googleapis.com/css2?family=Open+Sans:wght@300;400;600;700&family=Raleway:wght@300;400;500;600&display=swap" rel="stylesheet">
<style>
:root{
  --black:#0b0b0b;
  --pink:#e6007e;
  --purple:#8a00c8;
  --dark:#333333;
  --text:#555555;
  --muted:#8a8a8a;
  --line:#e3e3e3;
  --soft:#f4f4f6;
  --white:#ffffff;
  --footer:#1e1e1e;
  --star:#f0b400;
}
*{box-sizing:border-box;margin:0;padding:0}
html,body{width:1200px;height:3087px;overflow:hidden}
body{position:relative;background:var(--white);font-family:"Open Sans",Arial,sans-serif;color:var(--text)}
.abs{position:absolute}

/* header */
.site-header{position:absolute;left:0;top:0;width:1200px;height:90px;background:var(--black);border-bottom:5px solid var(--pink)}
.nav-link{position:absolute;top:37px;color:var(--white);font-size:12px;letter-spacing:.5px}
.icon-btn{position:absolute;top:24px;width:42px;height:42px;border:2px solid var(--white);border-radius:50%}
.icon-btn svg{position:absolute;left:11px;top:11px}
.brand{position:absolute;left:549px;top:12px;width:100px;text-align:center;color:var(--white);font-family:"Raleway",sans-serif;font-weight:600;font-size:50px;line-height:60px}

/* hero */
.hero{position:absolute;left:0;top:95px;width:1200px;height:485px;overflow:hidden}
.hero-photo{position:absolute;inset:0;background:linear-gradient(90deg,#f7f7f9 0%,#f2f1f4 50%,#e6e1ea 75%,#dcd3e2 100%)}
.hero-title{position:absolute;left:86px;top:100px;font-family:"Raleway",sans-serif;font-weight:300;font-size:60px;color:var(--dark);line-height:1}
.hero-sub{position:absolute;left:86px;top:176px;width:480px;font-size:16.5px;line-height:26px;color:var(--pink)}
.hero-body{position:absolute;left:86px;top:246px;width:460px;font-size:11.5px;line-height:22px;color:var(--muted)}
.hero-dots{position:absolute;left:1144px;top:190px}
.hero-dots span{display:block;width:14px;height:14px;border:1.5px solid #999;border-radius:50%;margin-bottom:7px}
.hero-dots span.on{border-color:var(--pink)}

/* categories */
.category{position:absolute;top:603px;width:334px;height:224px}
.category .ph{position:absolute;inset:0}
.category .tag{position:absolute;left:50px;top:154px;width:234px;height:50px;background:rgba(70,70,70,.75);color:var(--white);font-family:"Raleway",sans-serif;font-size:21px;line-height:50px;text-align:center}

/* featured */
.featured{position:absolute;left:0;top:854px;width:1200px;height:926px;background:var(--soft)}
.section-title{font-family:"Raleway",sans-serif;font-weight:400;font-size:21px;color:var(--dark);letter-spacing:.3px}
.section-title em{font-style:normal;color:var(--pink)}
.ctl-label{position:absolute;top:30px;font-size:10px;color:var(--muted)}
.ctl-select{position:absolute;top:52px;height:22px;background:var(--white);border:1px solid var(--line);font-size:9.5px;color:var(--muted);padding:4px 6px}
.ctl-select:after{content:"▾";position:absolute;right:6px;top:3px;font-size:10px;color:var(--dark)}
.view-btn{position:absolute;top:52px;width:22px;height:22px;background:var(--white);border:1px solid var(--line)}
.view-btn.on{background:var(--pink);border-color:var(--pink)}
.product{position:absolute;width:242px;height:375px;background:var(--white);border:1px solid #ececec}
.product .ph{position:absolute;left:8px;top:8px;width:224px;height:272px;background:linear-gradient(180deg,#fbfbfb,#eeeeef)}
.product .sale{position:absolute;right:8px;top:16px;width:46px;height:46px;border-radius:50%;background:var(--pink);color:var(--white);font-size:10px;font-weight:600;line-height:46px;text-align:center}
.product .stars{position:absolute;left:0;top:290px;width:100%;text-align:center;color:var(--star);font-size:11px;letter-spacing:1px}
.product .name{position:absolute;left:0;top:314px;width:100%;text-align:center;font-family:"Raleway",sans-serif;font-size:17px;color:var(--dark)}
.product .swatches{position:absolute;left:0;top:345px;width:100%;text-align:center;font-size:0}
.swatches i{display:inline-block;width:13px;height:13px;border-radius:50%;margin:0 2px}
.sw-pink{background:var(--pink)}.sw-dark{background:var(--dark)}.sw-purple{background:var(--purple)}

/* welcome */
.welcome{position:absolute;left:0;top:1780px;width:1200px;height:406px}
.welcome .ph{position:absolute;left:0;top:0;width:535px;height:406px;background:linear-gradient(180deg,#cfcbc6 0%,#b3aea8 60%,#6a6561 100%)}
.welcome .panel{position:absolute;left:535px;top:0;width:665px;height:406px;background:linear-gradient(180deg,var(--pink) 0%,#d9006f 100%)}
.welcome h2{position:absolute;left:41px;top:83px;font-family:"Raleway",sans-serif;font-weight:400;font-size:23px;color:var(--white)}
.welcome p{position:absolute;left:41px;top:134px;width:510px;font-size:11.5px;line-height:23.5px;color:var(--white)}
.welcome .btn{position:absolute;left:41px;top:290px;width:227px;height:46px;border:2px solid var(--white);color:var(--white);font-size:12px;line-height:42px;text-align:center}

/* blog */
.blog-head{position:absolute;left:0;top:2228px;width:1200px;text-align:center}
.blog-sub{position:absolute;left:0;top:2270px;width:1200px;text-align:center;font-size:11px;color:var(--text)}
.post{position:absolute;top:2313px;width:326px}
.post .ph{height:206px}
.post h3{margin-top:32px;font-family:"Raleway",sans-serif;font-weight:400;font-size:16px;color:var(--dark)}
.post .meta{margin-top:10px;height:38px;border-top:1px solid var(--line);border-bottom:1px solid var(--line);display:flex;align-items:center;gap:32px;font-size:8.5px;color:var(--muted)}
.post p{margin-top:22px;font-size:11.5px;line-height:23px;color:var(--text)}

/* footer */
.site-footer{position:absolute;left:0;top:2747px;width:1200px;height:340px;background:var(--footer);color:var(--white)}
.f-col{position:absolute;top:56px}
.f-col h4{font-size:13px;font-weight:700;letter-spacing:.5px;margin-bottom:26px}
.f-col li{list-style:none;font-size:11px;line-height:26px;padding-left:26px;position:relative}
.f-col li:before{content:"›";position:absolute;left:0;top:0;font-weight:700}
.cards{display:flex;gap:3px}
.cards span{width:39px;height:25px;background:#e9e9e9;border-radius:2px}
.cards span:nth-child(2){background:#d4d4d4}.cards span:nth-child(3){background:#bfcfe0}.cards span:nth-child(4){background:#dad6cf}
.socials{display:flex;gap:7px;margin-top:46px}
.socials span{width:36px;height:36px;border:1.5px solid var(--white);border-radius:50%}
.contact li{padding-left:30px}
.contact li:before{content:none}
.contact svg{position:absolute;left:0;top:7px}
.f-rule{position:absolute;left:0;top:268px;width:1200px;border-top:1px solid #333}
.copyright{position:absolute;left:0;top:296px;width:1200px;text-align:center;font-size:11px;color:#ccc}
</style>
</head>
<body>

<header class="site-header">
  <span class="icon-btn" style="left:114px"><svg width="16" height="16" viewBox="0 0 16 16"><path d="M1 2h2.5l2 8h7l1.5-6H5" fill="none" stroke="#fff" stroke-width="1.6"/><circle cx="6.5" cy="13" r="1.3" fill="#fff"/><circle cx="12" cy="13" r="1.3" fill="#fff"/></svg></span>
  <span class="nav-link" style="left:190px">HOME</span>
  <span class="nav-link" style="left:284px">ABOUT US</span>
  <span class="nav-link" style="left:403px">SERVICES</span>
  <span class="brand">vey</span>
  <span class="nav-link" style="left:716px">PRODUCTS</span>
  <span class="nav-link" style="left:840px">BLOG</span>
  <span class="nav-link" style="left:932px">CONTACT US</span>
  <span class="icon-btn" style="left:1050px"><svg width="16" height="16" viewBox="0 0 16 16"><circle cx="6.5" cy="6.5" r="4.5" fill="none" stroke="#fff" stroke-width="1.8"/><path d="M10 10l4.5 4.5" stroke="#fff" stroke-width="1.8"/></svg></span>
</header>

<section class="hero">
  <div class="hero-photo" role="img" aria-label="Woman in patterned leggings lying on a yoga mat with legs raised in a shoulder stand"></div>
  <h1 class="hero-title">vey yoga</h1>
  <p class="hero-sub">Sed ut perspiciatis unde omnis iste natus error sit voluptatem accusantium architecto</p>
  <p class="hero-body">Sed ut perspiciatis unde omnis iste natus error sit voluptatem accusantium dolor em que laudantium, totam rem aperiam, eaque ipsa quae ab illo inventore veritatis et quasi architecto beatae vitae dicta sunt explicabo.</p>
  <div class="hero-dots"><span></span><span></span><span class="on"></span><span></span><span></span></div>
</section>

<a class="category" style="left:86px"><div class="ph" role="img" aria-label="Woman lying on a yoga mat in leggings" style="background:linear-gradient(135deg,#b9c3c8,#7f98a3)"></div><span class="tag">YOGA LEGGINGS</span></a>
<a class="category" style="left:434px"><div class="ph" role="img" aria-label="Woman in stylish leggings posing against a brick wall" style="background:linear-gradient(135deg,#a46a4f,#6e4636)"></div><span class="tag">STYLISH LEGGINGS</span></a>
<a class="category" style="left:782px"><div class="ph" role="img" aria-label="Women in yoga tops stretching on mats" style="background:linear-gradient(135deg,#2f4b5d,#5c5f66)"></div><span class="tag">WOMEN YOGA TOPS</span></a>

<section class="featured">
  <h2 class="section-title abs" style="left:84px;top:42px">FEATURED <em>PRODUCTS</em></h2>
  <span class="ctl-label" style="left:788px">Filter :</span>
  <span class="ctl-label" style="left:912px">Sort By :</span>
  <span class="ctl-label" style="left:1035px">View :</span>
  <span class="ctl-select" style="left:788px;width:103px">Payment..</span>
  <span class="ctl-select" style="left:912px;width:98px">Order</span>
  <svg class="abs" style="left:1015px;top:56px" width="10" height="14" viewBox="0 0 10 14"><path d="M5 1v12M1.5 4.5L5 1l3.5 3.5" fill="none" stroke="#333" stroke-width="1.5"/></svg>
  <span class="view-btn" style="left:1035px"></span>
  <span class="view-btn on" style="left:1060px"></span>
  <span class="view-btn" style="left:1085px"></span>

  <div class="product" style="left:88px;top:105px"><div class="ph" role="img" aria-label="Model in black leggings in triangle pose"></div><span class="sale">SALE</span><div class="stars">★★★★☆</div><div class="name">YOGA LEGGINGS</div><div class="swatches"><i class="sw-pink"></i><i class="sw-dark"></i><i class="sw-purple"></i></div></div>
  <div class="product" style="left:350px;top:105px"><div class="ph" role="img" aria-label="Model in lime leggings and pink top holding a resistance band"></div><div class="stars">★★★★☆</div><div class="name">YOGA LEGGINGS</div><div class="swatches"><i class="sw-pink"></i><i class="sw-dark"></i><i class="sw-purple"></i></div></div>
  <div class="product" style="left:611px;top:105px"><div class="ph" role="img" aria-label="Model in black leggings with a water bottle"></div><span class="sale">SALE</span><div class="stars">★★★★☆</div><div class="name">YOGA LEGGINGS</div><div class="swatches"><i class="sw-pink"></i><i class="sw-dark"></i><i class="sw-purple"></i></div></div>
  <div class="product" style="left:870px;top:105px"><div class="ph" role="img" aria-label="Model in grey leggings and black top"></div><div class="stars">★★★★☆</div><div class="name">YOGA LEGGINGS</div><div class="swatches"><i class="sw-pink"></i><i class="sw-dark"></i><i class="sw-purple"></i></div></div>

  <div class="product" style="left:88px;top:506px"><div class="ph" role="img" aria-label="Model in black cropped leggings"></div><div class="stars">★★★★☆</div><div class="name">YOGA LEGGINGS</div><div class="swatches"><i class="sw-pink"></i><i class="sw-dark"></i><i class="sw-purple"></i></div></div>
  <div class="product" style="left:350px;top:506px"><div class="ph" role="img" aria-label="Model in black leggings and red top"></div><span class="sale">SALE</span><div class="stars">★★★★☆</div><div class="name">YOGA LEGGINGS</div><div class="swatches"><i class="sw-pink"></i><i class="sw-dark"></i><i class="sw-purple"></i></div></div>
  <div class="product" style="left:611px;top:506px"><div class="ph" role="img" aria-label="Model in blue top stretching on a mat"></div><div class="stars">★★★★☆</div><div class="name">YOGA LEGGINGS</div><div class="swatches"><i class="sw-pink"></i><i class="sw-dark"></i><i class="sw-purple"></i></div></div>
  <div class="product" style="left:870px;top:506px"><div class="ph" role="img" aria-label="Model in dancer pose on a mat"></div><span class="sale">SALE</span><div class="stars">★★★★☆</div><div class="name">YOGA LEGGINGS</div><div class="swatches"><i class="sw-pink"></i><i class="sw-dark"></i><i class="sw-purple"></i></div></div>
</section>

<section class="welcome">
  <div class="ph" role="img" aria-label="Woman in green leggings doing a forearm balance on a yoga mat"></div>
  <div class="panel">
    <h2>WELCOME TO VEY</h2>
    <p>Sed ut perspiciatis unde omnis iste natus error sit voluptatem accusantium doloremque laudantium, totam rem aperiam, eaque ipsa quae ab illo inventore veritatis et quasi arch itecto beatae vitae dicta sunt explicabo. Nemo enim ipsam voluptatem quia voluptas sit aspernatur aut odit aut fugit, sed quia consequuntur magni dolores eos qui ratione volup beatae vitae dicta sunt tatem sequi nesciunt.</p>
    <a class="btn">CLICK HERE FOR MORE INFO</a>
  </div>
</section>

<h2 class="section-title blog-head">LATEST <em>BLOG</em></h2>
<p class="blog-sub">Sed ut perspiciatis unde omnis iste natus error sit voluptatem accusantium doloremque laudantium</p>

<article class="post" style="left:86px">
  <div class="ph" role="img" aria-label="Woman seated on a yoga mat in a twist" style="background:linear-gradient(180deg,#b1b5b8,#8e979b)"></div>
  <h3>SED UT PERSPICIATIS..</h3>
  <div class="meta"><span>◷ 27 MARCH 2016</span><span>◌ 120</span><span>♡ LIKE</span><span>↗ SHARE</span></div>
  <p>Voluptatem accusantium doloremque laudantium, totam rem aperiam, eaque ipsa quae ab illo inventore veritatis et quia voluptas sit aspernatur nesciunt.</p>
</article>
<article class="post" style="left:438px">
  <div class="ph" role="img" aria-label="Woman stretching on a mat in a bright studio" style="background:linear-gradient(180deg,#f5efe6,#e4d6c2)"></div>
  <h3>SED UT PERSPICIATIS..</h3>
  <div class="meta"><span>◷ 27 MARCH 2016</span><span>◌ 120</span><span>♡ LIKE</span><span>↗ SHARE</span></div>
  <p>Voluptatem accusantium doloremque laudantium, totam rem aperiam, eaque ipsa quae ab illo inventore veritatis et quia voluptas sit aspernatur nesciunt.</p>
</article>
<article class="post" style="left:788px">
  <div class="ph" role="img" aria-label="Woman balancing in a plank variation on a mat" style="background:linear-gradient(180deg,#eeecec,#d9d2cb)"></div>
  <h3>SED UT PERSPICIATIS..</h3>
  <div class="meta"><span>◷ 27 MARCH 2016</span><span>◌ 120</span><span>♡ LIKE</span><span>↗ SHARE</span></div>
  <p>Voluptatem accusantium doloremque laudantium, totam rem aperiam, eaque ipsa quae ab illo inventore veritatis et quia voluptas sit aspernatur nesciunt.</p>
</article>

<footer class="site-footer">
  <div class="f-col" style="left:93px">
    <h4>PAYMENTS ACCEPTED</h4>
    <div class="cards"><span></span><span></span><span></span><span></span></div>
    <div class="socials"><span></span><span></span><span></span><span></span><span></span></div>
  </div>
  <div class="f-col" style="left:360px">
    <h4>INFORMATION</h4>
    <ul><li>About us</li><li>Customer Service</li><li>Company</li><li>Investor Relations</li><li>Advanced Search</li></ul>
  </div>
  <div class="f-col" style="left:566px">
    <h4>WHY CHOOSE US</h4>
    <ul><li>Shopping Guide</li><li>Blog</li><li>Company</li><li>Investor Relations</li><li>Contact Us</li></ul>
  </div>
  <div class="f-col" style="left:753px">
    <h4>MY ACCOUNT</h4>
    <ul><li>My account</li><li>Orders</li><li>Addresses</li><li>Shopping cart</li><li>Wishlist</li></ul>
  </div>
  <div class="f-col contact" style="left:936px">
    <h4>CONTACT US</h4>
    <ul>
      <li><svg width="13" height="12" viewBox="0 0 13 12"><rect x="0" y="2" width="13" height="10" rx="2" fill="#fff"/><rect x="3" y="0" width="7" height="4" rx="1" fill="#fff"/></svg>(000)-121-1231 (Phone)</li>
      <li><svg width="13" height="12" viewBox="0 0 13 12"><rect x="0" y="4" width="13" height="6" rx="1" fill="#fff"/><rect x="3" y="0" width="7" height="4" fill="#fff"/><rect x="3" y="8" width="7" height="4" fill="#ccc"/></svg>(000)-121-1231 &nbsp;&nbsp;(Fax)</li>
      <li><svg width="13" height="10" viewBox="0 0 13 10"><rect x=".5" y=".5" width="12" height="9" fill="none" stroke="#fff"/><path d="M.5 .5l6 5 6-5" fill="none" stroke="#fff"/></svg><u>info@vey.example</u></li>
      <li style="line-height:16px;padding-top:5px"><svg width="11" height="14" viewBox="0 0 11 14" style="top:6px"><path d="M5.5 0a5 5 0 0 1 5 5c0 4-5 9-5 9s-5-5-5-9a5 5 0 0 1 5-5z" fill="#fff"/><circle cx="5.5" cy="5" r="2" fill="#1e1e1e"/></svg>#254 Lorem Ipsum Dummy<br>Text Lorem Ipsum</li>
    </ul>
  </div>
  <div class="f-rule"></div>
  <p class="copyright">© Copyright 2016 Vey yoga.All Rights Reserved</p>
</footer>

</body>
</html>
```